Verlindo Magician

I want the business card for my business to give to people who watch that later I will be employed to show magic here is my website http://www.verlindoillusions.example/I want the interesting design , i am very opened for formal and informal, I watch a lot of design so don't stick to the common shape and form but i hope it can also be produced the thing to write on will be the same as in picture that i will upload , i also will upload the logo for you that so can be easy to useDenis CostilleMagicianMAGICIAN BALSAMO 17 rue des Tilleuls - 99450 VERMONTEL contact@verlindoillusions.example tel. 0199 946 157 tel. 0199 219 503

```html
<!DOCTYPE html>
<html lang="en">
<head>
<meta charset="utf-8">
<title>Verlindo Magician – Business Cards</title>
<link href="https://fonts.googleapis.com/css2?family=Jost:wght@300;400;500&display=swap" rel="stylesheet">
<style>
  :root {
    --backdrop: #3b3b3b;
    --card-dark: #1f1f1f;
    --card-light: #f1f1f1;
    --ink-white: #ffffff;
    --ink-dark: #1a1a1a;
    --ink-grey: #bdbdbd;
    --accent-red: #e3262d;
    --portrait-light: #ececec;
    --portrait-dark: #151515;
  }
  * { margin: 0; padding: 0; box-sizing: border-box; }
  html, body {
    width: 1200px; height: 800px; overflow: hidden;
    background: var(--backdrop);
    font-family: "Jost", "Futura", sans-serif;
  }
  .card-set {
    position: relative; width: 1200px; height: 800px;
    display: flex; justify-content: center; align-items: center; gap: 44px;
  }
  .card {
    width: 340px; height: 550px; border-radius: 22px; overflow: hidden;
    position: relative; display: flex; flex-direction: column; align-items: center;
  }
  .card--back { background: var(--card-dark); color: var(--ink-white); }
  .card--front { background: var(--card-light); color: var(--ink-dark); }

  .portrait {
    width: 220px; height: 250px; margin-top: 42px; border-radius: 46% 46% 18% 18%;
  }
  .card--back .portrait { background: linear-gradient(180deg, var(--portrait-light), #d6d6d6); }
  .card--front .portrait { background: linear-gradient(180deg, #2a2a2a, var(--portrait-dark)); margin-top: 78px; height: 280px; }

  .contact { margin-top: 26px; text-align: center; }
  .contact__name {
    color: var(--accent-red); font-size: 25px; font-weight: 400;
    text-transform: uppercase; letter-spacing: 0.3px; line-height: 1;
  }
  .contact__role {
    color: var(--ink-grey); font-size: 13px; letter-spacing: 2px; margin-top: 4px;
  }
  .contact__details { margin-top: 16px; font-size: 15px; font-weight: 300; line-height: 1.3; }
  .contact__phone { display: flex; justify-content: center; align-items: center; gap: 5px; font-size: 17px; }
  .contact__phone svg { width: 11px; height: 11px; fill: var(--accent-red); }
  .contact__address { margin-top: 14px; font-size: 14px; font-weight: 300; }

  .wordmark { margin-top: 22px; text-align: center; font-weight: 300; color: var(--ink-dark); line-height: 1; }
  .wordmark__name { font-size: 50px; letter-spacing: 1px; }
  .wordmark__tag { font-size: 14px; letter-spacing: 2px; margin-top: 4px; }
</style>
</head>
<body>
  <main class="card-set">
    <section class="card card--back">
      <div class="portrait" role="img" aria-label="Illustrated portrait of the magician holding a playing card, white on black"></div>
      <div class="contact">
        <h1 class="contact__name">Marc Ravoulet</h1>
        <p class="contact__role">MAGICIAN</p>
        <div class="contact__details">
          <p class="contact__phone"><svg viewBox="0 0 24 24" aria-hidden="true"><path d="M6.6 10.8a15.1 15.1 0 0 0 6.6 6.6l2.2-2.2a1 1 0 0 1 1-.25 11.4 11.4 0 0 0 3.6.57 1 1 0 0 1 1 1V20a1 1 0 0 1-1 1A17 17 0 0 1 3 4a1 1 0 0 1 1-1h3.5a1 1 0 0 1 1 1c0 1.25.2 2.45.57 3.57a1 1 0 0 1-.25 1z"/></svg>0199 946 157</p>
          <p class="contact__phone"><svg viewBox="0 0 24 24" aria-hidden="true"><path d="M6.6 10.8a15.1 15.1 0 0 0 6.6 6.6l2.2-2.2a1 1 0 0 1 1-.25 11.4 11.4 0 0 0 3.6.57 1 1 0 0 1 1 1V20a1 1 0 0 1-1 1A17 17 0 0 1 3 4a1 1 0 0 1 1-1h3.5a1 1 0 0 1 1 1c0 1.25.2 2.45.57 3.57a1 1 0 0 1-.25 1z"/></svg>0199 219 503</p>
          <p class="contact__email">contact@verlindoillusions.example</p>
          <p class="contact__web">www.verlindoillusions.example</p>
        </div>
        <p class="contact__address">17 rue des Tilleuls - 99450 VERMONTEL</p>
      </div>
    </section>

    <section class="card card--front">
      <div class="portrait" role="img" aria-label="Illustrated portrait of the magician holding a playing card, black on white"></div>
      <div class="wordmark">
        <p class="wordmark__name">VERLINDO</p>
        <p class="wordmark__tag">MAGICIEN</p>
      </div>
    </section>
  </main>
</body>
</html>
```